A website for a Maltese Law Firm

Our law firm needs a website to further its business. The site should have a simple yet effective design. We would need the following sections: About us, Practice Areas, About Malta, Contact. These should be further split as follows:

About us: Our firm, Our values, What others say, Offices

Practice Areas: Crimimal, Citizenship & Residence, Sovereign Patron Pathway, Criminal Defence, Civil Litigation, Arbitration and ADR, Commercial and Corporate, Media Law.

About Malta: just one section.

Contact: Just one section

We would also need a news feed at the front of the site to include latest news regarding our cases.

At the bottom we need a section for our Terms and a Privacy Statement.

Our logo is being attached.

Target Market(s)

All clients looking for legal assistance in Malta

Industry/Entity Type

Legal

Coding

Coded - Design and coding required

Number of Pages Required

1 page

Requirements
Must have
• It must be simple yet striking.

```html
<!DOCTYPE html>
<html lang="en">
<head>
<meta charset="utf-8">
<title>Brincat &amp; Zammit Advocates</title>
<link href="https://fonts.googleapis.com/css2?family=Cinzel:wght@400;500;600&family=Lato:ital,wght@0,400;0,700;1,400&display=swap" rel="stylesheet">
<style>
:root{
  --ink:#2a2b33;
  --dark:#26272e;
  --text:#333338;
  --muted:#55565c;
  --light:#ececec;
  --white:#ffffff;
  --band:#a9aaae;
  --nav-active:#b9babd;
  --line:#d0d0d0;
}
*{box-sizing:border-box;margin:0;padding:0}
html,body{width:1200px;height:2723px;overflow:hidden}
body{position:relative;background:var(--white);font-family:"Lato",Arial,sans-serif;color:var(--text)}
.heading{font-family:"Cinzel",Georgia,serif;font-weight:500;color:var(--ink)}
.site-header,.main-nav,.hero,.welcome,.practice,.cases,.testimonials,.cta,.site-footer{position:absolute;left:0;width:1200px}

/* header */
.site-header{top:0;height:107px;background:var(--white)}
.brand{position:absolute;left:70px;top:22px;font-family:"Cinzel",Georgia,serif;font-size:26px;font-weight:500;color:var(--ink);line-height:1;white-space:nowrap;border-top:2px solid var(--ink);border-bottom:2px solid var(--ink);padding:12px 2px 14px}
.header-contact{position:absolute;left:898px;top:24px;font-size:16px;font-weight:700;color:var(--ink)}
.header-contact div{display:flex;align-items:center;gap:12px;height:34px}
.header-contact svg{width:26px;height:26px}

/* nav */
.main-nav{top:107px;height:45px;background:var(--ink);display:flex;padding-left:68px}
.main-nav a{display:flex;align-items:center;padding:0 22px;font-family:"Cinzel",Georgia,serif;font-size:15px;color:var(--white);text-decoration:none;border-right:1px solid #55565e;letter-spacing:.3px}
.main-nav a.active{background:var(--nav-active);color:var(--ink)}

/* hero */
.hero{top:152px;height:426px}
.hero-image{position:absolute;inset:0;background:linear-gradient(100deg,#3d3025 0%,#7d6b5a 45%,#a08e7b 60%,#5d4a3a 100%)}
.hero-title{position:absolute;left:70px;top:72px;font-family:"Cinzel",Georgia,serif;font-size:36px;line-height:41px;color:var(--white);font-weight:500}
.hero-btn{position:absolute;left:68px;top:264px;width:404px;height:50px;border:2px solid #c9c9c9;background:rgba(80,80,85,.55);color:var(--white);font-family:"Cinzel",Georgia,serif;font-size:23px;display:flex;align-items:center;justify-content:center}
.slide-arrow{position:absolute;width:20px;height:30px}

/* welcome */
.welcome{top:578px;height:452px;background:var(--light)}
.welcome h1{position:absolute;left:70px;top:60px;font-size:29px;white-space:nowrap}
.welcome .lead{position:absolute;left:70px;top:114px;width:680px;font-size:16px;line-height:24px;color:var(--ink)}
.welcome .body{position:absolute;left:70px;top:176px;width:680px;font-size:13.5px;line-height:21.5px;color:var(--ink)}
.pill-btn{position:absolute;display:flex;align-items:center;height:30px;background:var(--band);border:1px solid #777;border-radius:3px;font-size:12px;font-weight:700;color:var(--ink);padding-left:10px}
.pill-btn .go{position:absolute;right:-2px;top:-3px;width:34px;height:34px;border-radius:50%;background:var(--ink);display:flex;align-items:center;justify-content:center}
.eval-box{position:absolute;left:797px;top:62px;width:331px;height:325px;border:2px solid var(--ink);padding:22px 16px}
.eval-box h2{font-size:23px;margin-bottom:18px;white-space:nowrap}
.field{height:40px;background:var(--white);border:1px solid var(--line);border-radius:3px;margin:0 0 9px 0;font-size:12px;padding:10px;color:var(--muted)}
.field.tall{height:76px}

/* practice */
.practice{top:1030px;height:425px;background:var(--white)}
.section-title{position:absolute;left:0;width:1200px;text-align:center;font-size:29px}
.practice-item{position:absolute;top:123px;width:270px;text-align:center}
.practice-icon{width:102px;height:102px;margin:0 auto;border:3px solid var(--ink);display:flex;align-items:center;justify-content:center}
.practice-icon.active{background:var(--ink)}
.practice-item h3{font-size:20px;margin-top:18px;white-space:nowrap}
.practice-item p{font-size:13.5px;line-height:18px;margin-top:8px;padding:0 28px}
.practice-item .more{font-size:14px;margin-top:10px}
.chev{position:absolute;top:215px;width:22px;height:62px}

/* cases */
.cases{top:1455px;height:527px;background:var(--light)}
.case{position:absolute;top:120px;width:312px}
.case-photo{height:160px;border:6px solid var(--white);outline:1px solid #c8c8c8;position:relative}
.case-date{position:absolute;left:6px;top:6px;width:45px;background:var(--white);text-align:center}
.case-date b{display:block;background:var(--ink);color:var(--white);font-size:16px;line-height:22px}
.case-date span{font-size:13px;line-height:20px}
.case h3{font-size:13px;font-weight:700;margin-top:14px;color:var(--ink)}
.case p{font-size:12.5px;line-height:18px;margin-top:10px}
.case .read{font-size:12px;margin-top:10px}

/* testimonials */
.testimonials{top:1982px;height:300px;background:var(--white)}
.client-photo{position:absolute;left:135px;top:118px;width:115px;height:118px;background:linear-gradient(180deg,#c6ccd3,#8e969f)}
.quote{position:absolute;left:320px;top:118px;width:750px;font-size:13.5px;line-height:22px;font-style:italic;color:var(--ink)}
.quote-mark{position:absolute;font-family:Georgia,serif;font-size:60px;color:#dcdcdc;line-height:1}
.client-name{position:absolute;left:307px;top:222px;font-family:"Cinzel",Georgia,serif;font-size:18px;color:var(--ink)}

/* cta */
.cta{top:2282px;height:130px;background:var(--band)}
.cta h2{position:absolute;left:115px;top:28px;font-family:"Cinzel",Georgia,serif;font-weight:500;font-size:29px;line-height:36px;color:var(--white)}
.cta-btn{position:absolute;left:844px;top:40px;width:224px;height:48px;background:var(--ink);border:2px solid #d7d7d7;color:var(--white);font-weight:700;font-size:23px;display:flex;align-items:center;justify-content:center}

/* footer */
.site-footer{top:2412px;height:266px;background:var(--dark);color:var(--white)}
.foot-title{position:absolute;top:42px;font-family:"Cinzel",Georgia,serif;font-size:17px;padding-bottom:8px;border-bottom:1px solid #4b4c54}
.quick-links{position:absolute;left:70px;top:86px;list-style:none;font-size:12px;font-weight:700;line-height:24.5px}
.quick-links li::before{content:"•";margin-right:8px}
.map{position:absolute;left:302px;top:82px;width:260px;height:128px;background:linear-gradient(135deg,#e4e6e3,#cfd6d2)}
.contact-list{position:absolute;left:590px;top:82px;font-size:12px;font-weight:700;line-height:18px}
.contact-list div{display:flex;gap:12px;margin-bottom:9px}
.contact-list svg{width:14px;height:14px;flex:none;margin-top:2px}
.foot-brand{position:absolute;left:868px;top:92px;font-family:"Cinzel",Georgia,serif;font-size:16px;line-height:1;color:var(--white);white-space:nowrap;border-top:1px solid #8b8c92;border-bottom:1px solid #8b8c92;padding:8px 2px}
.social{position:absolute;left:924px;top:150px;display:flex;gap:11px}
.social span{width:32px;height:32px;border-radius:50%;border:2px solid var(--white);background:#3a5a9a}
.social span:nth-child(2){background:#1876b5}
.social span:nth-child(3){background:#2a9ad4}
.social span:nth-child(4){background:#d1462f}
.legal-bar{position:absolute;top:2678px;left:0;width:1200px;height:45px;background:#d6d6d8;font-size:12.5px;color:var(--ink);display:flex;align-items:center;justify-content:space-between;padding:0 70px}
.legal-links{display:flex;align-items:center;gap:0}
.legal-links a{color:var(--ink);text-decoration:none;margin:0 10px}
.legal-links a:last-child{margin-right:0}
</style>
</head>
<body>

<header class="site-header">
  <div class="brand">Brincat &amp; Zammit Advocates</div>
  <div class="header-contact">
    <div><svg viewBox="0 0 26 26"><rect x="1" y="1" width="24" height="24" rx="4" fill="#2a2b33"/><rect x="8" y="5" width="10" height="16" rx="1.5" fill="none" stroke="#fff" stroke-width="2"/></svg>356-2100-4477</div>
    <div><svg viewBox="0 0 26 26"><rect x="1" y="1" width="24" height="24" rx="4" fill="#2a2b33"/><rect x="6" y="8" width="14" height="10" fill="none" stroke="#fff" stroke-width="1.6"/><path d="M6 8l7 6 7-6" fill="none" stroke="#fff" stroke-width="1.6"/></svg>info@brincatzammit.com</div>
  </div>
</header>

<nav class="main-nav">
  <a class="active" href="#">Home</a>
  <a href="#">About Malta</a>
  <a href="#">Practice Areas</a>
  <a href="#">Our Firm</a>
  <a href="#">Our Values</a>
  <a href="#">What Others Say</a>
  <a href="#">Contact Us</a>
</nav>

<section class="hero">
  <div class="hero-image" role="img" aria-label="Bronze scales of justice on a dark wooden background"></div>
  <h2 class="hero-title">Realize Your<br>Constitutional<br>Right For Qualified<br>Legal Help</h2>
  <div class="hero-btn">Get A Free Consultation</div>
  <svg class="slide-arrow" style="left:22px;top:176px" viewBox="0 0 20 30"><path d="M15 4L5 15l10 11" fill="none" stroke="#fff" stroke-width="3"/></svg>
  <svg class="slide-arrow" style="left:1160px;top:176px" viewBox="0 0 20 30"><path d="M5 4l10 11L5 26" fill="none" stroke="#fff" stroke-width="3"/></svg>
</section>

<section class="welcome">
  <h1 class="heading">Welcome To Brincat &amp; Zammit Advocates</h1>
  <p class="lead">Lorem ipsum dolor sit amet, consectetuer adipiscing elit, sed diam nonummy nibh euismod tincidunt ut laoreet dolore magna aliquam erat volutpat.</p>
  <p class="body">Lorem ipsum dolor sit amet, consectetur adipiscing elit. Sed vitae magna tellus. Aenean ante nunc, semper nec cursus non, rutrum ac eros. Vestibulum mattis justo ac dui bibendum consequat a ac ipsum. Praesent a arcu venenatis, auctor velit eu, suscipit libero. Quisque convallis, leo ac pharetra sagittis, ipsum arcu auctor urna, sit amet cursus risus augue in eros. Duis lacinia nisi vitae leo commodo, non finibus magna maximus. Sed posuere, neque eget bibendum pulvinar, ligula erat suscipit dolor, ut maximus arcu mi et tortor. Quisque imperdiet turpis et ligula mollis ultricies. Mauris lacinia rhoncus odio, at rutrum diam mollis eu. Quisque ut ipsum faucibus, tristique dui vitae, posuere orci.</p>
  <div class="pill-btn" style="left:70px;top:359px;width:122px">READ MORE<span class="go"><svg width="10" height="12" viewBox="0 0 10 12"><path d="M2 1l6 5-6 5" fill="none" stroke="#fff" stroke-width="2"/></svg></span></div>
  <form class="eval-box">
    <h2 class="heading">Free Case Evaluation</h2>
    <div class="field" style="margin-left:17px">Name</div>
    <div class="field" style="margin-left:17px">Email</div>
    <div class="field tall" style="margin-left:17px">Message</div>
    <div class="pill-btn" style="left:17px;top:268px;width:120px">SUBMIT<span class="go"><svg width="10" height="12" viewBox="0 0 10 12"><path d="M2 1l6 5-6 5" fill="none" stroke="#fff" stroke-width="2"/></svg></span></div>
  </form>
</section>

<section class="practice">
  <h2 class="heading section-title" style="top:66px">Our Practice Areas</h2>
  <svg class="chev" style="left:30px" viewBox="0 0 22 62"><path d="M18 2L4 31l14 29" fill="none" stroke="#555" stroke-width="2"/></svg>
  <svg class="chev" style="left:1150px" viewBox="0 0 22 62"><path d="M4 2l14 29L4 60" fill="none" stroke="#555" stroke-width="2"/></svg>
  <div class="practice-item" style="left:65px">
    <div class="practice-icon"><svg width="50" height="40" viewBox="0 0 50 40"><circle cx="14" cy="24" r="10" fill="none" stroke="#2a2b33" stroke-width="5"/><circle cx="36" cy="24" r="10" fill="none" stroke="#2a2b33" stroke-width="5"/></svg></div>
    <h3 class="heading">Crimimal</h3>
    <p>Lorem ipsum dolor sit amet, consectetuer Lorem dolor sit amet, consectetuer</p>
    <div class="more">[+]</div>
  </div>
  <div class="practice-item" style="left:323px">
    <div class="practice-icon active"><svg width="40" height="54" viewBox="0 0 40 54"><rect x="2" y="2" width="36" height="50" rx="4" fill="#fff"/><circle cx="20" cy="22" r="8" fill="none" stroke="#2a2b33" stroke-width="2"/><rect x="12" y="38" width="16" height="3" fill="#2a2b33"/></svg></div>
    <h3 class="heading">Citizenship &amp; Residence</h3>
    <p>Lorem ipsum dolor sit amet, consectetuer Lorem dolor sit amet, consectetuer</p>
    <div class="more">[+]</div>
  </div>
  <div class="practice-item" style="left:595px">
    <div class="practice-icon"><svg width="50" height="50" viewBox="0 0 50 50"><rect x="8" y="20" width="34" height="22" fill="#2a2b33"/><circle cx="25" cy="13" r="7" fill="#2a2b33"/></svg></div>
    <h3 class="heading">Criminal Defence</h3>
    <p>Lorem ipsum dolor sit amet, consectetuer Lorem dolor sit amet, consectetuer</p>
    <div class="more">[+]</div>
  </div>
  <div class="practice-item" style="left:868px">
    <div class="practice-icon"><svg width="50" height="50" viewBox="0 0 50 50"><rect x="14" y="8" width="16" height="12" transform="rotate(-40 22 14)" fill="#2a2b33"/><rect x="22" y="18" width="5" height="22" transform="rotate(-40 24 29)" fill="#2a2b33"/><rect x="4" y="42" width="26" height="5" fill="#2a2b33"/></svg></div>
    <h3 class="heading">Civil Litigation</h3>
    <p>Lorem ipsum dolor sit amet, consectetuer Lorem dolor sit amet, consectetuer</p>
    <div class="more">[+]</div>
  </div>
</section>

<section class="cases">
  <h2 class="heading section-title" style="top:56px">Case Studies</h2>
  <article class="case" style="left:68px">
    <div class="case-photo" role="img" aria-label="Shelf of leather-bound law books" style="background:linear-gradient(90deg,#4a2a14,#8c6a30,#5a3a1c)"><div class="case-date"><b>06</b><span>Jun</span></div></div>
    <h3>Lorem Ipsum Dolor Sit Amet  Consectetur</h3>
    <p>Lorem ipsum dolor sit amet, consectetur adipiscing elit. Sed vitae magna tellus. Aenean ante nunc, semper nec cursus non, rutrum ac eros.</p>
    <div class="read">Read More ››</div>
  </article>
  <article class="case" style="left:444px">
    <div class="case-photo" role="img" aria-label="Courtroom with a handcuffed defendant" style="background:linear-gradient(90deg,#5a2c1a,#3c3a3c,#2c2c30)"><div class="case-date"><b>06</b><span>Jun</span></div></div>
    <h3>Lorem Ipsum Dolor Sit Amet  Consectetur</h3>
    <p>Lorem ipsum dolor sit amet, consectetur adipiscing elit. Sed vitae magna tellus. Aenean ante nunc, semper nec cursus non, rutrum ac eros.</p>
    <div class="read">Read More ››</div>
  </article>
  <article class="case" style="left:816px">
    <div class="case-photo" role="img" aria-label="Hands signing a legal document" style="background:linear-gradient(90deg,#2a2a2e,#c8c8c8,#e6e6e6)"><div class="case-date"><b>07</b><span>Jun</span></div></div>
    <h3>Lorem Ipsum Dolor Sit Amet  Consectetur</h3>
    <p>Lorem ipsum dolor sit amet, consectetur adipiscing elit. Sed vitae magna tellus. Aenean ante nunc, semper nec cursus non, rutrum ac eros.</p>
    <div class="read">Read More ››</div>
  </article>
  <div class="pill-btn" style="left:538px;top:450px;width:120px">&nbsp;&nbsp;VIEW ALL<span class="go"><svg width="10" height="12" viewBox="0 0 10 12"><path d="M2 1l6 5-6 5" fill="none" stroke="#fff" stroke-width="2"/></svg></span></div>
</section>

<section class="testimonials">
  <h2 class="heading section-title" style="top:58px">Client Testimonials</h2>
  <svg class="chev" style="left:30px;top:140px" viewBox="0 0 22 62"><path d="M18 2L4 31l14 29" fill="none" stroke="#555" stroke-width="2"/></svg>
  <svg class="chev" style="left:1150px;top:140px" viewBox="0 0 22 62"><path d="M4 2l14 29L4 60" fill="none" stroke="#555" stroke-width="2"/></svg>
  <div class="client-photo" role="img" aria-label="Portrait of the client"></div>
  <span class="quote-mark" style="left:305px;top:100px">“</span>
  <p class="quote">Lorem ipsum dolor sit amet, consectetuer adipiscing elit, sed diam nonummy nibh euismod tincidunt ut laoreet dolore magna aliquam erat volutpat. Ut wisi enim ad minim veniam, quis nostrud exerci iriure dolor in Lorem ipsum dolor sit amet, consectetuer adipiscing elit, sed diam nonummy nibh euismod tincidunt ut laoreet dolore magna aliquam erat volutpat. Ut wisi enim ad minim veniam, quis nostrud exerci iriure dolor.</p>
  <span class="quote-mark" style="left:538px;top:172px">”</span>
  <div class="client-name">- Daniel Ross</div>
</section>

<section class="cta">
  <h2>For Any Legal Problem, We Can Help You<br>Anytime take An Appointment Now</h2>
  <div class="cta-btn">CONTACT US</div>
</section>

<footer class="site-footer">
  <div class="foot-title" style="left:68px;width:140px">Quick Links</div>
  <ul class="quick-links">
    <li>Home</li><li>About Malta</li><li>Practice Areas</li><li>Our Firm</li><li>Our Values</li><li>What Others Say</li><li>Contact Us</li>
  </ul>
  <div class="foot-title" style="left:302px;width:488px">Contact Details</div>
  <div class="map" role="img" aria-label="Street map showing the office location"></div>
  <div class="contact-list">
    <div><svg viewBox="0 0 14 14"><path d="M7 1a4 4 0 0 1 4 4c0 3-4 8-4 8S3 8 3 5a4 4 0 0 1 4-4z" fill="#fff"/></svg><span>Brincat &amp; Zammit Advocates<br>12/4, Merchants Lane, Valletta<br>88, Orchard Road, Mosta</span></div>
    <div><svg viewBox="0 0 14 14"><path d="M3 1l3 3-2 2a8 8 0 0 0 4 4l2-2 3 3-2 2C6 13 1 8 1 3z" fill="#fff"/></svg><span>356-2100-448</span></div>
    <div><svg viewBox="0 0 14 14"><rect x="1" y="4" width="12" height="7" fill="#fff"/><rect x="3" y="1" width="8" height="3" fill="#fff"/></svg><span>356-2100-448</span></div>
    <div><svg viewBox="0 0 14 14"><rect x="1" y="3" width="12" height="8" fill="#fff"/><path d="M1 3l6 5 6-5" fill="none" stroke="#26272e" stroke-width="1.3"/></svg><span>info@brincatzammit.com</span></div>
  </div>
  <div class="foot-brand">Brincat &amp; Zammit Advocates</div>
  <div class="social"><span></span><span></span><span></span><span></span></div>
</footer>

<div class="legal-bar">
  <div>Copyright © 2016 <b>Brincat &amp; Zammit Advocates</b>. All Rights Reserved.</div>
  <div class="legal-links"><a href="#">Terms &amp; Conditions</a>|<a href="#">Privacy Policy</a>|<a href="#">Disclaimer</a></div>
</div>

</body>
</html>
```